Business card design for international hub site

I need a business card design with the logo attached. Although the site is for the teenage audience (it is about the high school graduation ball, the Prom), the business card is for professional use to be given to professional contacts (B2B), such as suppliers and partners, so it needs to look professional (but also girly, glamours and clean).

Target Market(s)

B2B

Industry/Entity Type

Media

Colors
eea4c8
f9d9e8
e667a6
9d9d9d
1b1b1b

Requirements
Must have
• Space for Name, Tile, Address, Phone, email and website.
Should not have
• Photo

```html
<!DOCTYPE html>
<html lang="en">
<head>
<meta charset="utf-8">
<title>Gala Glow — Business Card</title>
<link rel="stylesheet" href="https://fonts.googleapis.com/css2?family=Arimo:wght@400;700&display=swap">
<style>
  :root {
    --stage: #1b1b1b;
    --card-magenta: #d21f6e;
    --card-rose: #c42a7c;
    --card-violet: #9a2fa3;
    --ink-white: #ffffff;
    --ink-soft: #f9d9e8;
    --accent-pink: #e667a6;
  }
  * { box-sizing: border-box; margin: 0; padding: 0; }
  html, body {
    width: 1200px;
    height: 997px;
    overflow: hidden;
    background: var(--stage);
    font-family: "Arimo", Arial, sans-serif;
  }
  .stage {
    width: 1200px;
    height: 997px;
    position: relative;
  }
  .card {
    position: absolute;
    width: 540px;
    height: 310px;
    border-radius: 22px;
    overflow: hidden;
    color: var(--ink-white);
  }
  .card-texture {
    position: absolute;
    inset: 0;
    background:
      radial-gradient(ellipse at 20% 80%, rgba(255,120,150,0.35), transparent 60%),
      linear-gradient(120deg, var(--card-magenta) 0%, var(--card-rose) 50%, var(--card-violet) 100%);
  }
  .card-front { left: 50px; top: 160px; }
  .card-back  { left: 610px; top: 527px; }

  .brand-name {
    position: absolute;
    font-weight: 400;
    color: var(--ink-white);
    letter-spacing: 1px;
    white-space: nowrap;
  }
  .card-front .brand-name {
    font-size: 52px;
    left: 0; right: 0;
    top: 100px;
    text-align: center;
  }
  .front-website {
    position: absolute;
    right: 40px;
    bottom: 36px;
    font-size: 15px;
    color: var(--ink-soft);
    letter-spacing: 0.5px;
  }

  .card-back .brand-name {
    font-size: 30px;
    left: 150px;
    top: 34px;
  }
  .holder {
    position: absolute;
    right: 36px;
    top: 118px;
    text-align: left;
  }
  .holder-name {
    font-size: 17px;
    font-weight: 700;
    letter-spacing: 0.5px;
  }
  .holder-title {
    font-size: 13px;
    margin-top: 4px;
    color: var(--ink-soft);
  }
  .divider {
    position: absolute;
    left: 36px;
    right: 36px;
    top: 170px;
    height: 1.5px;
    background: var(--ink-white);
  }
  .contact-list {
    position: absolute;
    left: 36px;
    top: 186px;
    list-style: none;
    font-size: 14px;
    line-height: 1.25;
  }
  .contact-item {
    display: flex;
    align-items: flex-start;
    gap: 10px;
    margin-bottom: 7px;
  }
  .contact-icon {
    flex: none;
    width: 16px;
    height: 16px;
  }
</style>
</head>
<body>
<main class="stage">

  <section class="card card-front" aria-label="Business card front">
    <div class="card-texture" role="img" aria-label="Pink to violet glitter texture"></div>
    <div class="brand-name">Gala Glow</div>
    <div class="front-website">www.galaglowhub.com</div>
  </section>

  <section class="card card-back" aria-label="Business card back">
    <div class="card-texture" role="img" aria-label="Pink to violet glitter texture"></div>
    <div class="brand-name">Gala Glow</div>

    <div class="holder">
      <div class="holder-name">MARA ELLISON</div>
      <div class="holder-title">Marketing Director</div>
    </div>

    <div class="divider"></div>

    <ul class="contact-list">
      <li class="contact-item">
        <svg class="contact-icon" viewBox="0 0 16 16" aria-hidden="true">
          <circle cx="8" cy="8" r="8" fill="#fff"/>
          <path d="M5 4.5h1.6l.7 2-1 .8a5 5 0 0 0 2.4 2.4l.8-1 2 .7v1.6c0 .4-.4.7-.8.7A6.5 6.5 0 0 1 4.3 5.3c0-.4.3-.8.7-.8z" fill="#d21f6e"/>
        </svg>
        <span>(877) 555-0142</span>
      </li>
      <li class="contact-item">
        <svg class="contact-icon" viewBox="0 0 16 16" aria-hidden="true">
          <circle cx="8" cy="8" r="8" fill="#fff"/>
          <rect x="5.5" y="3.5" width="5" height="9" rx="1" fill="#d21f6e"/>
          <rect x="6.3" y="4.5" width="3.4" height="6" fill="#fff"/>
        </svg>
        <span>(706) 555-0198</span>
      </li>
      <li class="contact-item">
        <svg class="contact-icon" viewBox="0 0 16 16" aria-hidden="true">
          <circle cx="8" cy="8" r="8" fill="#fff"/>
          <rect x="4" y="5" width="8" height="6" rx="0.8" fill="#d21f6e"/>
          <path d="M4.3 5.4 8 8.3l3.7-2.9" stroke="#fff" stroke-width="0.9" fill="none"/>
        </svg>
        <span>mellison@galaglowhub.com</span>
      </li>
      <li class="contact-item">
        <svg class="contact-icon" viewBox="0 0 16 16" aria-hidden="true">
          <circle cx="8" cy="8" r="8" fill="#fff"/>
          <path d="M8 3.5a3 3 0 0 0-3 3c0 2.2 3 6 3 6s3-3.8 3-6a3 3 0 0 0-3-3z" fill="#d21f6e"/>
          <circle cx="8" cy="6.5" r="1.1" fill="#fff"/>
        </svg>
        <span>480 Linden Court, 3rd Floor<br>Marlow, GA 30215</span>
      </li>
    </ul>
  </section>

</main>
</body>
</html>
```